Web Design Concept for new social network

We need a fresh, vibrant, clean web design layout for a new social network that we are trying to put together.
The site itself will be stuffed with little jquery/css tricks to enable a better/better looking UI (this is where you come in).
Imagine you were re-imagining Rallyhub.. How would you have designed it? The new site, will have a lot of similar functions to RH, and then a few more.
I will need a great looking sign in page in addition to;
The main page will need to have the following elements;
- Profile header.
Profile picture and tabbed area for various pieces of meta data contact details, preferences etc
- A Post Wall (like the wall on RH, but its crossed with a chirply-esque global search/post). People can respond to not only the original message, but can reply to each individual reply.
Instead of LIKE, there will need to be a positive/negative/neutral style option (feel free to get creative with naming). The background of each post will reflect the average rating (pos/nuetral/neg) of the post itself.. so if 100 people click pos, 50 neutral and 1 negative, the bg will mainly be the positive colour).
The feed will include messages by default from many sources (rallyhub/chirply/work loop) there should be somewhere that these can be switched on and off...
Somewhere to post a message - again by default it will post to all networks, but should be able to switch off.
Images/Videos/Text can all be posted to the wall (if you can think of a better name than wall - please use that!)
- Notifications; rather than having them in a drop down menu like rh, i want them to be in a hidden div (one div for each type) that slides open to reveal the notifications.. The default will be that the divs are closed so if there is a new notification there will be a need for something to appear on the screen that the user can click. We will need 3 notification types.
- Calendar; collapsable
- Options for today/this week/month views etc
- Menu system to navigate to other screens.
This should be able to show available things like groups/pages/events (again feel free to rename).
The screens themselves should appear to be stacked (like stacked tiles).
- Search; there should be a search bar somewhere with various options being available.
- Modal popup. I will be using modal popups across the site so will want a consistant feel (should be able to display photos/videos etc)
I will upload some files over the next few days to support the above, but am really looking for your creativity here.
Sites I really like the style of:
- the NEW yardnook (check it out.. its awesome).
- quince
- chirply
I want a really clean interface, modern.. splashes of colour are fine (but only where it will enhance).
Updates
I have added a file to the uploads that gives an idea of how the notifications should be revealed.. Please do not read too much into any styling... i created the pdf just to show how i expect the notifications to be revealed, and that I expect there to be multiple notification types.
Although I deliberately didnt request adverts to be shown in the brief, i also didnt explicitly state that they shouldnt be! The site will NOT feature adverts so please do not show them on the design. Id much rather that the space be used to improve layout.
Target Market(s)
18 to 40 - again, think rallyhub/chirply/workloop
Industry/Entity Type
Events
Look and feel

```html
<!DOCTYPE html>
<html lang="en">
<head>
<meta charset="utf-8">
<title>Huddlespot — Sign in</title>
<link rel="stylesheet" href="https://fonts.googleapis.com/css2?family=Ubuntu:wght@400;500;700&family=Arimo:wght@400;700&display=swap">
<style>
  :root {
    --ink: #3f3f3f;
    --ink-soft: #6a6a6a;
    --ink-faint: #a6a6a6;
    --page-light: #f6f7f9;
    --white: #ffffff;
    --field: #f2f2f2;
    --field-edge: #d6d6d6;
    --green-top: #86ad1c;
    --green-mid: #6e9512;
    --green-deep: #4c6d08;
    --green-field: #4a6a07;
    --green-field-edge: #2f5400;
    --bubble: #ffffff;
    --bubble-text: #7a7a7a;
  }
  * { box-sizing: border-box; margin: 0; padding: 0; }
  html, body { width: 1200px; height: 707px; overflow: hidden; }
  body {
    font-family: "Ubuntu", sans-serif;
    color: var(--ink);
    background: var(--white);
    position: relative;
  }

  /* Header */
  .site-header {
    position: absolute; left: 0; top: 0; width: 1200px; height: 101px;
    background: linear-gradient(#ffffff, #f7f7f8);
    border-top: 1px solid #dcdcdc;
    border-bottom: 1px solid #e4e5e7;
  }
  .brand {
    position: absolute; left: 125px; top: 22px; height: 52px;
    display: flex; align-items: center; gap: 14px;
  }
  .brand-square { width: 48px; height: 52px; background: #4b4b4b; }
  .brand-name { font-size: 22px; font-weight: 700; color: #5a5a5a; letter-spacing: -0.3px; white-space: nowrap; }

  .quick-login { position: absolute; top: 0; left: 0; width: 1200px; height: 101px; }
  .quick-label { position: absolute; top: 23px; font-size: 14px; color: var(--ink-soft); white-space: nowrap; }
  .quick-field {
    position: absolute; top: 46px; width: 218px; height: 26px;
    background: var(--field); border: 1px solid var(--field-edge); border-radius: 2px;
    box-shadow: inset 0 1px 2px rgba(0,0,0,.06);
  }
  .quick-button {
    position: absolute; left: 1016px; top: 46px; width: 69px; height: 27px;
    background: linear-gradient(#9cc62c, #5f8a0c); border-radius: 3px;
    color: #fff; font-size: 12px; font-weight: 700; border: 1px solid #557d08;
    display: flex; align-items: center; justify-content: center;
  }
  .quick-note {
    position: absolute; top: 81px; font-size: 12px; line-height: 14px;
    color: var(--ink-faint); white-space: nowrap;
  }
  .remember-dot {
    display: inline-block; width: 9px; height: 9px; border-radius: 50%;
    background: #f0f0f0; border: 1px solid #e0e0e0; margin-right: 5px; vertical-align: -1px;
  }
  .language {
    position: absolute; left: 996px; top: 7px; font-size: 13px; color: #b9b9b9;
    display: flex; align-items: center; gap: 8px; white-space: nowrap;
  }
  .language span { text-decoration: underline; }

  /* Hero */
  .hero {
    position: absolute; left: 0; top: 101px; width: 1200px; height: 549px;
    background: linear-gradient(#e7e8eb 0%, var(--page-light) 45%, #edeff2 100%);
  }
  .tagline {
    position: absolute; left: 126px; top: 45px;
    font-size: 22px; line-height: 27px; font-weight: 400; color: #454545; letter-spacing: .2px;
    white-space: nowrap;
  }
  .world-map {
    position: absolute; left: 35px; top: 130px; width: 670px; height: 350px;
    background: radial-gradient(ellipse at 50% 45%, #dcdfe3 0%, #e2e4e8 55%, rgba(230,232,236,0) 75%);
  }
  .status-bubble {
    position: absolute; background: var(--bubble); border-radius: 3px;
    box-shadow: 0 1px 3px rgba(0,0,0,.14); padding: 5px 6px 5px 46px;
    font-family: "Ubuntu", sans-serif; font-size: 7.5px; line-height: 8px;
    color: var(--bubble-text); font-weight: 500; letter-spacing: -0.1px;
  }
  .status-bubble::after {
    content: ""; position: absolute; left: 74px; bottom: -5px;
    border: 5px solid transparent; border-bottom: 0; border-top-color: var(--bubble);
  }
  .avatar { position: absolute; left: 6px; top: 6px; width: 34px; height: 34px; background: linear-gradient(#b79c86, #7d6a5c); }
  .status-author { text-align: right; margin-top: 3px; font-weight: 400; white-space: nowrap; }

  /* Sign up */
  .signup {
    position: absolute; left: 705px; top: 50px; width: 375px; height: 420px;
    border-radius: 3px; color: #fff;
    background:
      radial-gradient(ellipse at 60% 25%, rgba(160,200,40,.55), rgba(0,0,0,0) 60%),
      linear-gradient(160deg, var(--green-top) 0%, var(--green-mid) 50%, var(--green-deep) 100%);
    box-shadow: 0 4px 14px rgba(0,0,0,.25);
  }
  .signup-title { position: absolute; left: 19px; top: 36px; font-size: 38px; font-weight: 700; white-space: nowrap; }
  .signup-intro { position: absolute; left: 19px; top: 91px; width: 340px; font-size: 12px; line-height: 15px; }
  .field-row { position: absolute; left: 0; width: 375px; height: 37px; }
  .field-label {
    position: absolute; right: 261px; top: 0; line-height: 37px;
    font-family: "Arimo", sans-serif; font-size: 11px; white-space: nowrap;
  }
  .field-input {
    position: absolute; left: 125px; top: 0; width: 213px; height: 37px;
    background: var(--green-field); border: 1px solid var(--green-field-edge);
    font-family: "Arimo", sans-serif; font-size: 14px; line-height: 35px; padding-left: 7px;
    white-space: nowrap; overflow: hidden;
  }
  .field-input.secret { letter-spacing: 1px; font-size: 15px; }
  .signup-options {
    position: absolute; left: 128px; top: 316px; font-family: "Arimo", sans-serif; font-size: 11px;
    display: flex; align-items: center; white-space: nowrap;
  }
  .checkbox { width: 12px; height: 12px; background: linear-gradient(#fff, #d8d8e0); border: 1px solid #8c8ca0; margin-right: 6px; }
  .forgot { margin-left: 27px; text-decoration: underline; }
  .signup-button {
    position: absolute; left: 126px; top: 350px; width: 99px; height: 38px;
    background: linear-gradient(#ffffff, #dcdcdc); border-radius: 4px; border: 1px solid #c4c4c4;
    font-family: "Arimo", sans-serif; font-size: 13px; font-weight: 700; color: #3a3a3a;
    display: flex; align-items: center; justify-content: center;
  }

  /* Footer */
  .site-footer {
    position: absolute; left: 0; top: 650px; width: 1200px; height: 57px; background: var(--white);
    font-size: 12px; color: #555;
  }
  .copyright { position: absolute; left: 120px; top: 22px; white-space: nowrap; }
  .footer-nav { position: absolute; right: 120px; top: 22px; display: flex; gap: 25px; }
  .footer-nav a { color: #555; text-decoration: none; }
</style>
</head>
<body>
  <header class="site-header">
    <div class="brand">
      <span class="brand-square"></span>
      <span class="brand-name">Huddlespot.com</span>
    </div>

    <div class="quick-login">
      <span class="quick-label" style="left:563px">Username</span>
      <span class="quick-label" style="left:789px">Password</span>
      <span class="quick-field" style="left:564px"></span>
      <span class="quick-field" style="left:790px"></span>
      <span class="quick-button">Login</span>
      <span class="quick-note" style="left:570px"><span class="remember-dot"></span>Remember me</span>
      <span class="quick-note" style="left:801px">Forget password</span>
    </div>

    <div class="language">
      <svg width="17" height="17" viewBox="0 0 17 17" aria-hidden="true">
        <circle cx="8.5" cy="8.5" r="7.5" fill="none" stroke="#c4c4c4" stroke-width="1.5"/>
        <ellipse cx="8.5" cy="8.5" rx="3.2" ry="7.5" fill="none" stroke="#c4c4c4" stroke-width="1"/>
        <line x1="1" y1="8.5" x2="16" y2="8.5" stroke="#c4c4c4" stroke-width="1"/>
      </svg>
      <span>English</span>
      <svg width="10" height="6" viewBox="0 0 10 6" aria-hidden="true"><path d="M0 6 L5 0 L10 6Z" fill="#c8c8c8"/></svg>
    </div>
  </header>

  <main class="hero">
    <h1 class="tagline">Find out what’s happening,right now,<br>with the people and you care about</h1>

    <div class="world-map" role="img" aria-label="Dotted world map showing members around the globe"></div>

    <div class="status-bubble" style="left:101px;top:232px;width:157px">
      <span class="avatar" role="img" aria-label="Member profile photo"></span>
      Lorem ipsum dolor sit amet, consectetuer adipiscing elit, sed diam nonummy nibh euismod tincidunt ut laoreet
      <div class="status-author">- exerci tation ull</div>
    </div>
    <div class="status-bubble" style="left:314px;top:184px;width:158px">
      <span class="avatar" role="img" aria-label="Member profile photo"></span>
      Lorem ipsum dolor sit amet, consectetuer adipiscing elit, sed diam nonummy nibh euismod tincidunt ut laoreet
      <div class="status-author">- exerci tation ull</div>
    </div>
    <div class="status-bubble" style="left:516px;top:269px;width:158px">
      <span class="avatar" role="img" aria-label="Member profile photo"></span>
      Lorem ipsum dolor sit amet, consectetuer adipiscing elit, sed diam nonummy nibh
      <div class="status-author">- exerci tation ull</div>
    </div>

    <section class="signup">
      <h2 class="signup-title">Sign Up</h2>
      <p class="signup-intro">Lorem Ipsum is simply dummy text of the printing and type setting industry.</p>

      <div class="field-row" style="top:155px">
        <span class="field-label">Email:</span>
        <span class="field-input">yourname@inbox.test</span>
      </div>
      <div class="field-row" style="top:205px">
        <span class="field-label">Password:</span>
        <span class="field-input secret">●●●●●●●●●●●</span>
      </div>
      <div class="field-row" style="top:255px">
        <span class="field-label">Re-type Password</span>
        <span class="field-input secret">●●●●●●●●●●●</span>
      </div>

      <div class="signup-options">
        <span class="checkbox"></span>
        <span>Remember Me</span>
        <span class="forgot">Forgot password?</span>
      </div>
      <span class="signup-button">LOGIN</span>
    </section>
  </main>

  <footer class="site-footer">
    <span class="copyright">© 2012 Huddlespot. All Rights Reserved</span>
    <nav class="footer-nav">
      <a href="#">About</a><a href="#">Services</a><a href="#">Portfolio</a><a href="#">Blog</a><a href="#">Contact</a>
    </nav>
  </footer>
</body>
</html>
```